Flyer for Tallow Brisko - Design Agency

We need a 4-page square flyer measuring 14.8x14.8cm per page, to fold out, for a design agency targeting small businesses.
The design should be very modern. There shouldn't be too much content visible.
The background should be black. The color of the logo (attached) can also be used. The content is also attached and divided per page. We are open to alternative suggestions regarding the division.

```html
<!DOCTYPE html>
<html lang="de">
<head>
<meta charset="utf-8">
<title>Tallow Brisko – Faltflyer</title>
<link rel="stylesheet" href="https://fonts.googleapis.com/css2?family=Montserrat:wght@200;300;400;600&family=Quicksand:wght@400;500;600&display=swap">
<style>
  :root {
    --stage: #e3e3e1;
    --paper-black: #0b0b0c;
    --paper-gray: #2b2b2c;
    --teal: #5fd9cb;
    --blue: #2b8fd8;
    --magenta: #d93aa4;
    --white: #f2f2f2;
    --muted: #a9a9ab;
    --page: 280px;
  }
  * { box-sizing: border-box; margin: 0; padding: 0; }
  html, body { width: 1200px; height: 487px; overflow: hidden; }
  body {
    background: var(--stage);
    font-family: "Montserrat", sans-serif;
    color: var(--white);
    position: relative;
  }
  .spread {
    position: absolute;
    top: 103px;
    width: calc(var(--page) * 2);
    height: var(--page);
    display: flex;
    box-shadow: 0 6px 18px rgba(0,0,0,.18);
  }
  .spread--outside { left: 20px; }
  .spread--inside { left: 620px; }
  .page {
    position: relative;
    width: var(--page);
    height: var(--page);
    overflow: hidden;
  }
  .page--gray { background: var(--paper-gray); }
  .page--black { background: var(--paper-black); }

  .brand-name {
    font-family: "Quicksand", sans-serif;
    font-weight: 600;
    color: var(--teal);
    line-height: 1;
    letter-spacing: .01em;
  }

  /* Back cover */
  .back { padding: 26px 24px; }
  .back .brand-name { font-size: 26px; }
  .slogan {
    font-family: "Quicksand", sans-serif;
    font-weight: 600;
    font-size: 15px;
    line-height: 1.3;
    margin-top: 12px;
  }
  .cta {
    margin-top: 26px;
    font-size: 10px;
    line-height: 1.35;
    color: var(--blue);
    letter-spacing: .04em;
    text-transform: uppercase;
  }
  .contact {
    margin-top: 28px;
    font-size: 9px;
    line-height: 1.55;
    color: var(--white);
  }
  .contact .address { color: var(--blue); }
  .owners {
    position: absolute;
    left: 24px; bottom: 16px;
    font-size: 6.5px;
    color: var(--muted);
  }

  /* Front cover */
  .front { padding: 30px 26px; }
  .front .brand-name { font-size: 34px; }
  .front-claim {
    position: absolute;
    left: 26px; bottom: 30px;
    font-size: 11px;
    line-height: 1.35;
    font-weight: 300;
    letter-spacing: .03em;
  }
  .front-claim strong { font-weight: 600; }
  .claim-teal { color: var(--teal); }
  .claim-blue { color: var(--blue); }

  /* Inside left */
  .intro { padding: 34px 22px; }
  .triad {
    font-weight: 200;
    font-size: 25px;
    line-height: 1.05;
    letter-spacing: .03em;
    text-transform: uppercase;
  }
  .triad .modern { color: var(--white); }
  .triad .mutig { color: var(--teal); }
  .triad .markant { color: var(--blue); }
  .intro-brand {
    display: flex;
    align-items: center;
    gap: 8px;
    margin-top: 44px;
  }
  .intro-brand .brand-name { font-size: 15px; }
  .intro-brand p {
    font-size: 7.5px;
    line-height: 1.35;
    color: var(--teal);
    font-weight: 300;
  }
  .intro-text {
    margin-top: 24px;
    font-size: 8px;
    line-height: 1.5;
    font-weight: 300;
    max-width: 200px;
  }

  /* Inside right */
  .services { padding: 20px 22px 16px; }
  .section-title {
    font-size: 8.5px;
    font-weight: 600;
    letter-spacing: .06em;
    text-transform: uppercase;
    margin-bottom: 8px;
  }
  .service {
    display: flex;
    gap: 10px;
    margin-bottom: 9px;
  }
  .service svg { flex: none; width: 18px; height: 18px; margin-top: 2px; }
  .service h3 {
    font-size: 8.5px;
    font-weight: 400;
    color: var(--magenta);
    letter-spacing: .03em;
    text-transform: uppercase;
  }
  .service p {
    font-size: 6.8px;
    line-height: 1.4;
    color: var(--muted);
    font-weight: 300;
    max-width: 195px;
  }
  .why { margin-top: 10px; }
  .why ul { list-style: none; }
  .why li {
    position: relative;
    padding-left: 9px;
    font-size: 6.8px;
    line-height: 1.45;
    color: var(--muted);
    font-weight: 300;
    margin-bottom: 2px;
  }
  .why li::before {
    content: "";
    position: absolute;
    left: 0; top: 4px;
    width: 3px; height: 3px;
    border-radius: 50%;
    background: var(--magenta);
  }
  .guide-lines {
    position: absolute;
    inset: 0;
    pointer-events: none;
  }
</style>
</head>
<body>

<section class="spread spread--outside" aria-label="Außenseite">
  <article class="page page--gray back">
    <div class="brand-name">Tallow Brisko</div>
    <p class="slogan">Designs, die wirken.<br>Marken, die bleiben.</p>
    <p class="cta">Kontaktiere uns für eine<br>kostenlose Beratung!</p>
    <address class="contact">
      hallo@tallowbrisko.de<br>
      +49 123 98210<br>
      <span class="address">Lindenweg 8<br>60311 Frankfurt</span>
    </address>
    <p class="owners">Inhaber: Jonas Merel &amp; Tim Arvand</p>
  </article>
  <article class="page page--black front">
    <div class="brand-name">Tallow<br>Brisko</div>
    <p class="front-claim">
      Dein <strong>Unternehmen.</strong><br>
      <span class="claim-teal">Dein <strong>Stil.</strong></span><br>
      <span class="claim-blue">Unser <strong>Design.</strong></span>
    </p>
  </article>
</section>

<section class="spread spread--inside" aria-label="Innenseite">
  <article class="page page--black intro">
    <h1 class="triad">
      <span class="modern">Modern</span><br>
      <span class="mutig">Mutig</span><br>
      <span class="markant">Markant</span>
    </h1>
    <div class="intro-brand">
      <span class="brand-name">Tallow Brisko</span>
      <p>gestaltet die Zukunft deines<br>Unternehmensauftritts.</p>
    </div>
    <p class="intro-text">Wir machen aus Ideen visuelle Erlebnisse und sorgen dafür, dass deine Marke im Gedächtnis bleibt.</p>
  </article>

  <article class="page page--gray services">
    <h2 class="section-title">Unsere Leistungen:</h2>
    <div class="service">
      <svg viewBox="0 0 18 18" fill="none" stroke="#f2f2f2" stroke-width="1"><path d="M9 2c3 2 3 7 1.5 10h-3C6 9 6 4 9 2z"/><path d="M7.5 12l-2 3M10.5 12l2 3"/></svg>
      <div><h3>Next-Level Flyer</h3><p>Nicht nur Papier, sondern deine Botschaft im perfekten Look.</p></div>
    </div>
    <div class="service">
      <svg viewBox="0 0 18 18" fill="none" stroke="#f2f2f2" stroke-width="1"><circle cx="9" cy="9" r="7"/><circle cx="6" cy="7" r="1"/><circle cx="10" cy="5.5" r="1"/><circle cx="12.5" cy="9" r="1"/></svg>
      <div><h3>Corporate Identity</h3><p>Ein Design, das deine Marke spricht – individuell, stark, unvergesslich.</p></div>
    </div>
    <div class="service">
      <svg viewBox="0 0 18 18" fill="none" stroke="#f2f2f2" stroke-width="1"><circle cx="9" cy="9" r="7"/><ellipse cx="9" cy="9" rx="3" ry="7"/><path d="M2 9h14M3.5 5h11M3.5 13h11"/></svg>
      <div><h3>Digital &amp; Print</h3><p>Ob Social Media Grafiken oder klassisches Printdesign – wir sind da, wo du uns brauchst.</p></div>
    </div>
    <div class="service">
      <svg viewBox="0 0 18 18" fill="none" stroke="#f2f2f2" stroke-width="1"><path d="M9 2l2 4.5 5 .5-3.8 3.3 1.1 4.9L9 12.7 4.7 15.2l1.1-4.9L2 7l5-.5z"/></svg>
      <div><h3>Alles aus einer Hand</h3><p>Logo, Farben, Typografie, Flyer und vieles mehr – wir bauen das Fundament für deinen Erfolg.</p></div>
    </div>
    <div class="why">
      <h2 class="section-title">Warum wir?</h2>
      <ul>
        <li>Dein Style, unser Know-how: Wir kombinieren deine Vision mit moderner Ästhetik.</li>
        <li>Persönlicher Service: Wir hören zu und setzen um, was dich einzigartig macht.</li>
        <li>Flexible Lösungen für die unterschiedlichsten Anforderungen.</li>
      </ul>
    </div>
  </article>

  <svg class="guide-lines" viewBox="0 0 560 280" aria-hidden="true" fill="none" stroke-width=".8">
    <path d="M150 52H262V178H236" stroke="#f2f2f2"/>
    <path d="M118 78H274V200" stroke="#5fd9cb"/>
    <path d="M168 104H548V262H512" stroke="#2b8fd8"/>
    <path d="M440 148H538V186" stroke="#d93aa4"/>
    <path d="M452 160H520" stroke="#d93aa4"/>
  </svg>
</section>

</body>
</html>
```